Brintel Works - Fast, Efficient and Gas Mainteance for Domestic, Commercial and Industrial clients

We are in the process of purchasing a new business and would like to get a new logo and business card.
Business is a gas maintenance business that also does new gas installations.
Has been established since 1988.
Services include:
Install all types of gas appliances & equipment inc. hot water units
Maintain / repair / replace all types of gas appliances & equipment

Target Market(s)

Domestic, Commercial and Industrial clients

Industry/Entity Type

Business

Contact Information for Business Card

admin@brintelworks.com.au
07 3918 4726
Brintel Works PTY LTD

Logo Text

Gas Fitting & Plumbing Maintenance Specialists

Font styles to use
Sans Serif

Requirements
Must have
• Logo
• Business name, contact number, email address, web address
• Domestic | Commercial | Industrial Est Since 1988
Nice to have
• Possibly a black card with a flame logo to one side
Should not have
• Spelling errors

```html
<!DOCTYPE html>
<html lang="en">
<head>
<meta charset="utf-8">
<title>Brintel Works PTY LTD – Business Card</title>
<link rel="stylesheet" href="https://fonts.googleapis.com/css2?family=Source+Sans+3:wght@400;700&display=swap">
<style>
  :root {
    --backdrop: #999999;
    --card: #000000;
    --text: #ffffff;
    --brand: #f5a818;
    --icon: #f0a020;
    --flame-core: #f7b43a;
    --flame-mid: #e0701a;
    --flame-edge: #5a1a04;
  }
  * { margin: 0; padding: 0; box-sizing: border-box; }
  html, body {
    width: 1200px;
    height: 900px;
    overflow: hidden;
    background: var(--backdrop);
    font-family: "Source Sans 3", "Myriad Pro", sans-serif;
  }
  .stage { position: relative; width: 1200px; height: 900px; }
  .card {
    position: absolute;
    top: 275px;
    width: 477px;
    height: 294px;
    background: var(--card);
    color: var(--text);
    overflow: hidden;
  }
  .card--front { left: 116px; border-radius: 0 56px 0 56px; }
  .card--back  { left: 622px; border-radius: 56px 0 56px 0; }

  .brand-name {
    color: var(--brand);
    font-weight: 700;
    line-height: 1;
    white-space: nowrap;
  }
  .brand-suffix {
    color: var(--brand);
    font-weight: 700;
    letter-spacing: 2px;
    line-height: 1;
  }

  .front-brand {
    position: absolute;
    left: 0; right: 0;
    top: 128px;
    text-align: center;
  }
  .front-brand .brand-name { font-size: 27px; }
  .front-brand .brand-suffix { font-size: 11px; margin-top: 3px; }

  .contact-list {
    position: absolute;
    left: 0; right: 0;
    top: 187px;
    list-style: none;
    text-align: center;
    font-size: 14px;
    line-height: 20px;
  }
  .contact-list li { display: flex; justify-content: center; align-items: center; gap: 5px; }
  .contact-list svg { width: 10px; height: 10px; fill: var(--icon); }
  .contact-list .address { margin-top: 5px; }

  .back-brand {
    position: absolute;
    left: 25px;
    top: 156px;
    width: 292px;
    text-align: center;
  }
  .back-brand .brand-name { font-size: 37px; text-align: left; }
  .back-brand .brand-suffix { font-size: 13px; margin-top: 3px; }

  .sectors {
    position: absolute;
    left: 33px;
    top: 233px;
    font-size: 14px;
    white-space: nowrap;
  }

  .flame-photo {
    position: absolute;
    left: 338px;
    top: 10px;
    width: 136px;
    height: 275px;
    background: radial-gradient(ellipse 40% 55% at 55% 55%, var(--flame-core) 0%, var(--flame-mid) 45%, var(--flame-edge) 75%, transparent 100%);
    border-radius: 50% 50% 40% 40% / 70% 70% 30% 30%;
  }
</style>
</head>
<body>
<main class="stage">
  <section class="card card--front" aria-label="Card front">
    <div class="front-brand">
      <div class="brand-name">Brintel Works</div>
      <div class="brand-suffix">PTY LTD</div>
    </div>
    <ul class="contact-list">
      <li>
        <svg viewBox="0 0 10 10" aria-hidden="true"><path d="M2 0.5 L3.6 2.6 L2.8 3.6 Q4 6 6.4 7.2 L7.4 6.4 L9.5 8 L8.4 9.5 Q1.5 8 0.5 1.6 Z"/></svg>
        <span>07 3918 4726</span>
      </li>
      <li>
        <svg viewBox="0 0 10 10" aria-hidden="true"><path d="M0.5 2 H9.5 V8.5 H0.5 Z M1 2.5 L5 5.5 L9 2.5" stroke="#000" stroke-width="0.7"/></svg>
        <span>admin@brintelworks.com.au</span>
      </li>
      <li>
        <svg viewBox="0 0 10 10" aria-hidden="true"><path d="M4 6 L6 4 M3.5 4.5 L1.8 6.2 a1.5 1.5 0 0 0 2 2 L5.5 6.5 M6.5 5.5 L8.2 3.8 a1.5 1.5 0 0 0 -2 -2 L4.5 3.5" stroke="var(--icon)" stroke-width="1.2" fill="none"/></svg>
        <span>www.brintelworks.com.au</span>
      </li>
      <li class="address">12345, Address Goes Here Country Name, 123456</li>
    </ul>
  </section>

  <section class="card card--back" aria-label="Card back">
    <div class="back-brand">
      <div class="brand-name">Brintel Works</div>
      <div class="brand-suffix">PTY LTD</div>
    </div>
    <p class="sectors">Domestic | Commercial | Industrial Est Since 1988</p>
    <div class="flame-photo" role="img" aria-label="Photograph of a single orange flame rising against black"></div>
  </section>
</main>
</body>
</html>
```